Book covers for a 3 book series International Consultancy

We need book covers for our dangerous goods handbook series.

The 3 handbooks are for:
Shippers (Companies that ship dangerous goods)
Carriers (Companies that transport dangerous goods)
Tank (Companies that transport liquid dangerous goods)

Each cover should reflect the function the user of the book carries out.
Each cover should reflect that it is a part of a series (one customer could need all 3 books and needs to be able to tell them apart.

Each cover consists of and requires

Front:
1) Cover (Logo, name of company, name of book, version of book)
2) Front "flip out" (Text area & logo)

Back:
1) Back (ISBN bar code, 2 smaller logos (environmental, will be provided), company info (full name, address, phone, fax, email, web and VAT no)
2) Area to describe what we do = Chemical Compliance Consultancy (please contact me at teodor.halvmark@dk.lunacorvexa.com) for further material on what we do. We would like to see our icons (attached) in use to describe what we do.

Attached:
- Guidelines (3 separate files)
- Iconography
- Previous Cover

Hi all, Just a kind reminder about the end of the project: the dealine is wednesday. The earlier you submit your designs the better chances you'll have. Looking forward to seeing you great designs. Have a great monday. Stay caffeinated! ;) Best regards, Teodor

```html
<!DOCTYPE html>
<html lang="en">
<head>
<meta charset="utf-8">
<title>Dangerous Goods Tank – Handbook Cover</title>
<link rel="stylesheet" href="https://fonts.googleapis.com/css2?family=Open+Sans:ital,wght@0,300;0,400;0,700;0,800;1,600&display=swap">
<style>
  :root {
    --page-bg: #e8e5e0;
    --paper: #ffffff;
    --green-deep: #17602e;
    --green-mid: #237a3b;
    --green-bright: #2f9a48;
    --tab-green: #2a8c41;
    --ink-grey: #4a4a4a;
    --white: #ffffff;
    --photo-tanker: #8f9a94;
    --photo-tank: #d9dcd6;
  }
  * { margin: 0; padding: 0; box-sizing: border-box; }
  html, body {
    width: 1200px;
    height: 1122px;
    overflow: hidden;
    background: var(--page-bg);
    font-family: "Open Sans", Arial, sans-serif;
  }
  .cover {
    position: absolute;
    left: 225px;
    top: 41px;
    width: 750px;
    height: 1040px;
    background: var(--paper);
    overflow: hidden;
  }
  .cover-hero {
    position: absolute;
    left: 0;
    top: 0;
    width: 750px;
    height: 660px;
  }
  .edition {
    position: absolute;
    right: 34px;
    top: 34px;
    color: var(--white);
    font-weight: 700;
    font-size: 27px;
    letter-spacing: 0.5px;
  }
  .leaf {
    position: absolute;
  }
  .leaf--white {
    left: 86px;
    top: 222px;
    width: 70px;
    height: 110px;
    background: var(--white);
    border-radius: 0 60px 0 60px;
  }
  .leaf--tanker {
    left: 210px;
    top: 115px;
    width: 205px;
    height: 174px;
    border-radius: 0 90px 0 90px;
    background: linear-gradient(160deg, #b9c4bf 0%, var(--photo-tanker) 45%, #6f3a2c 70%, #55605a 100%);
    border: 3px solid var(--white);
  }
  .leaf--tank {
    left: 80px;
    top: 352px;
    width: 130px;
    height: 210px;
    border-radius: 90px 0 90px 0;
    background: linear-gradient(180deg, var(--photo-tank) 0%, #c3c8c1 60%, #a9b0a8 100%);
  }
  .title {
    position: absolute;
    left: 220px;
    top: 368px;
    color: var(--white);
    line-height: 1;
  }
  .title__series {
    display: block;
    font-weight: 300;
    font-size: 29px;
    letter-spacing: 0.5px;
  }
  .title__book {
    display: block;
    margin-top: 6px;
    font-weight: 800;
    font-size: 66px;
    letter-spacing: 1px;
  }
  .tabs {
    position: absolute;
    left: 0;
    top: 656px;
    width: 750px;
    height: 110px;
  }
  .brand {
    position: absolute;
    right: 34px;
    top: 905px;
    display: flex;
    align-items: center;
    gap: 10px;
  }
  .brand__mark {
    width: 22px;
    height: 22px;
    background: var(--ink-grey);
  }
  .brand__name {
    font-weight: 700;
    font-size: 22px;
    color: var(--ink-grey);
    letter-spacing: 1px;
  }
  .tagline {
    position: absolute;
    left: 245px;
    top: 942px;
    font-weight: 600;
    font-style: italic;
    font-size: 21px;
    color: var(--ink-grey);
  }
</style>
</head>
<body>
  <main class="cover">
    <svg class="cover-hero" viewBox="0 0 750 660" role="img" aria-label="Green-tinted photograph of a tanker truck on a road">
      <defs>
        <linearGradient id="heroTint" x1="0" y1="0" x2="1" y2="1">
          <stop offset="0" stop-color="#1f6f36"/>
          <stop offset="0.5" stop-color="#2a8a42"/>
          <stop offset="1" stop-color="#165a2b"/>
        </linearGradient>
      </defs>
      <path d="M0 0 H750 V200 L662 595 Q650 645 600 645 H0 Z" fill="url(#heroTint)"/>
    </svg>

    <div class="edition">ADR 2014/01</div>

    <div class="leaf leaf--white"></div>
    <div class="leaf leaf--tanker" role="img" aria-label="Photograph of a silver tanker lorry with red cab"></div>
    <div class="leaf leaf--tank" role="img" aria-label="Photograph of a white tank with a flammable hazard placard"></div>

    <h1 class="title">
      <span class="title__series">DANGEROUS GOODS</span>
      <span class="title__book">TANK</span>
    </h1>

    <svg class="tabs" viewBox="0 0 750 110" aria-hidden="true">
      <path d="M42 6 H290 Q302 6 298 18 L276 92 Q272 104 258 104 H20 Q8 104 12 92 L30 18 Q34 6 42 6 Z" fill="var(--tab-green)"/>
      <path d="M306 6 H540 Q552 6 548 18 L526 92 Q522 104 508 104 H284 Q272 104 276 92 L294 18 Q298 6 306 6 Z" fill="var(--tab-green)"/>
      <path d="M556 6 H750 V104 H534 Q522 104 526 92 L544 18 Q548 6 556 6 Z" fill="var(--tab-green)"/>
    </svg>

    <div class="brand">
      <span class="brand__mark"></span>
      <span class="brand__name">LUNACORVEXA</span>
    </div>

    <p class="tagline">Advance with Assurance</p>
  </main>
</body>
</html>
```